Design for a real estate wev portal

Contents and features of the site
---------------------------------
Website in 5 languages: French, Dutch, English, German, Spanish.
English name of the site: Harbor Nest Place
Main purpose of the site:
- allow people to rent their house/ appartment for flatsharing purposes.
- help people wanting to find a room in flatsharing
- help people to find additional roommates for their flatsharing
Key interaction sequence:
1. I create a "group" of people who have common interest/hobbies
2. People who have the same interests/hobbies join my group
3. I look for a house/appartment to host my group
Website structure will be the following:
- Home
- Groups
-- Look for a group
--- Join a group
-- Create a group
- Properties
-- Look for a house/appartement
-- Apply
- Sales conditions
- Contact
- My account
-- My profile
-- My groups OR my properties
Your mission
------------
The client has no graphical guidelines, simply a logo (see attached).
We need a (responsive compliant) design for the following pages (we expect PSD's from you. No HTML nor CSS):
1. homepage (see example and wireframe attached)
2. properties search result list (see wireframe attached)
3. "detailed" form for properties
4. groups search result list
5. "detailed" form for groups
6. my account page
FOR THE COMPETITION step we only expect from you the design of first 2 screens.
Based on that, we will select the designer who will win the project, and will have to design the 4 remaining screens.
Target Market(s)
B2C
Industry/Entity Type
Real Estate
Number of Pages Required
5+ page
Look and feel
Each slider illustrates characteristics of the customer's brand and the style your logo design should communicate.

```html
<!DOCTYPE html>
<html lang="en">
<head>
<meta charset="utf-8">
<title>Harbor Nest Place – Properties</title>
<link href="https://fonts.googleapis.com/css2?family=Dosis:wght@400;500;600;700&display=swap" rel="stylesheet">
<style>
:root{
  --teal:#1aa0b1;
  --teal-dark:#15899a;
  --ink:#3a3a3a;
  --muted:#6b6b6b;
  --line:#e3e3e3;
  --page:#f2f2f2;
  --white:#fff;
  --footer:#2b2b2b;
  --footer-text:#9a9a9a;
  --footer-head:#cfcfcf;
}
*{box-sizing:border-box;margin:0;padding:0}
html,body{width:1155px;height:1200px;overflow:hidden}
body{font-family:"Dosis",sans-serif;color:var(--ink);background:var(--page);position:relative;font-size:10px}
.abs{position:absolute}

/* header */
.site-header{position:absolute;left:0;top:0;width:1155px;height:127px;background:var(--white);border-bottom:1px solid #e6e6e6}
.brand{position:absolute;top:36px;left:0;width:1155px;text-align:center;font-size:22px;font-weight:600;color:var(--ink);letter-spacing:.5px}
.brand-dot{display:inline-block;width:14px;height:14px;border-radius:50%;background:var(--teal);vertical-align:-1px;margin-right:8px}
.auth{position:absolute;top:11px;height:22px;font-size:9.5px;font-weight:600;text-transform:uppercase;line-height:20px;text-align:center;border:1px solid var(--teal)}
.auth.register{left:791px;width:78px;color:var(--teal);background:var(--white)}
.auth.login{left:874px;width:47px;color:var(--white);background:var(--teal)}
.main-nav{position:absolute;top:96px;left:0;width:1155px;text-align:center;font-size:11.5px;font-weight:600;text-transform:uppercase;color:#444}
.main-nav span{margin:0 6px}
.main-nav .sep{margin:0 4px;color:#444}
.caret{font-size:7px;color:#999;vertical-align:2px}

/* panels */
.panel{position:absolute;background:var(--white);border:1px solid #e6e6e6}
.filters{left:235px;top:146px;width:156px;height:812px}
.results{left:400px;top:146px;width:520px;height:812px}

.f-title{position:absolute;left:11px;top:14px;font-size:11.5px;font-weight:600;text-transform:uppercase}
.f-label{position:absolute;left:11px;font-size:9.5px;color:#555}
.field{position:absolute;height:24px;border:1px solid #dcdcdc;font-size:9px;color:#666;display:flex;align-items:center;justify-content:center}
.search-field{left:11px;top:34px;width:133px;justify-content:flex-start;padding-left:10px;color:#999}
.slider-track{position:absolute;left:11px;top:96px;width:130px;height:3px;background:#ddd;border-radius:2px}
.slider-fill{position:absolute;left:0;top:0;width:82px;height:3px;background:var(--teal);border-radius:2px}
.slider-knob{position:absolute;left:79px;top:-2px;width:7px;height:7px;border-radius:50%;background:var(--teal)}
.slider-value{position:absolute;left:87px;top:106px;font-size:8.5px;color:var(--teal);font-style:italic}
.option{position:absolute;left:11px;font-size:9.5px;color:#555;display:flex;align-items:center}
.radio{width:11px;height:11px;border-radius:50%;border:1px solid #ccc;background:#f0f0f0;margin-right:8px;position:relative}
.radio.on::after{content:"";position:absolute;left:3px;top:3px;width:4px;height:4px;border-radius:50%;background:var(--teal)}
.divider{position:absolute;left:6px;top:580px;width:144px;height:3px;background:#e2e2e2}
.member-title{position:absolute;left:11px;top:602px;font-size:11px;font-weight:600;text-transform:uppercase;display:flex;align-items:center;gap:6px}
.member-text{position:absolute;left:11px;width:135px;font-size:9.5px;line-height:13.8px;color:#555}
.cta{position:absolute;left:11px;top:764px;width:126px;height:31px;background:var(--teal);color:var(--white);font-size:11px;font-weight:700;display:flex;align-items:center;justify-content:center}

/* results */
.results-head{position:absolute;left:18px;top:15px;font-size:11px;font-weight:600;color:#444}
.sort-label{position:absolute;left:347px;top:16px;font-size:9.5px;color:#555}
.sort-select{position:absolute;left:390px;top:9px;width:111px;height:25px;border:1px solid #dcdcdc;font-size:9px;color:#555;padding:0 10px;display:flex;align-items:center;justify-content:space-between}

.listing{position:absolute;left:18px;width:484px;height:165px;border:1px solid #e3e3e3;background:#fafafa}
.listing-photo{position:absolute;left:13px;top:10px;width:219px;height:144px}
.play{position:absolute;left:94px;top:56px;width:32px;height:32px;border-radius:50%;border:2px solid rgba(255,255,255,.85)}
.price{position:absolute;left:10px;top:13px;height:29px;padding:0 6px;background:var(--teal);color:var(--white);font-size:15px;font-weight:500;line-height:29px}
.price small{font-size:7px}
.listing-body{position:absolute;left:245px;top:12px;width:230px}
.addr{font-size:14.5px;color:#444;display:flex;align-items:center;gap:6px;white-space:nowrap}
.meta{display:flex;align-items:center;gap:16px;margin-top:7px;font-size:9px;color:#555}
.badge{background:var(--teal);color:var(--white);padding:0 10px;height:21px;line-height:21px;font-size:9px}
.avail{margin-top:10px;font-size:8.8px;color:#777;font-style:italic;display:flex;gap:18px}
.summary{margin-top:16px;font-size:8.8px;font-weight:700;color:#444;white-space:nowrap}
.excerpt{margin-top:3px;font-size:9px;line-height:14.5px;color:#555}
.tools{margin-top:4px;display:flex;gap:6px}

.ph1{background:linear-gradient(180deg,#3f73c4 0%,#8fb2de 45%,#d9b565 80%,#6e8f3e 100%)}
.ph2{background:linear-gradient(180deg,#4a86cf 0%,#9c7a45 45%,#7f6a45 65%,#5f9a34 100%)}
.ph3{background:linear-gradient(180deg,#d8dde2 0%,#a9b0b8 50%,#6a8a4f 80%,#c9412a 100%)}
.ph4{background:linear-gradient(180deg,#6e9ad0 0%,#dbe3ea 45%,#b9a77c 70%,#5a7a3c 100%)}

/* footer */
.site-footer{position:absolute;left:0;top:976px;width:1155px;height:224px;background:var(--footer)}
.f-head{position:absolute;top:46px;font-size:11.5px;font-weight:600;color:var(--footer-head);text-transform:uppercase}
.f-text{position:absolute;font-size:9.2px;line-height:16px;color:var(--footer-text)}
.f-links{position:absolute;list-style:none;font-size:9.2px;color:var(--footer-text);line-height:17.3px}
.f-links li::before{content:"›";margin-right:6px}
.f-info{position:absolute;left:645px;top:73px;width:130px;list-style:none;font-size:9.2px;color:var(--footer-text);line-height:12.5px}
.f-info li{padding-left:10px;text-indent:-10px;margin-bottom:5px}
.f-info li::before{content:"›";margin-right:6px}
.contact-line{position:absolute;left:798px;font-size:9.2px;color:var(--footer-text);line-height:14.5px;display:flex;gap:7px}
.contact-line svg{flex:none;margin-top:2px}
.footer-rule{position:absolute;left:235px;top:180px;width:686px;height:1px;background:#3d3d3d}
.copy{position:absolute;top:191px;font-size:10.5px;color:#6c6c6c}
</style>
</head>
<body>

<header class="site-header">
  <div class="auth register">Register here</div>
  <div class="auth login">Login</div>
  <div class="brand"><span class="brand-dot"></span>Harbor Nest Place</div>
  <nav class="main-nav">
    <span>Home</span><span class="sep">I</span>
    <span>Groups <span class="caret">▾</span></span><span class="sep">I</span>
    <span>Properties <span class="caret">▾</span></span><span class="sep">I</span>
    <span>Sales conditions</span><span class="sep">I</span>
    <span>Contact</span><span class="sep">I</span>
    <span>My account <span class="caret">▾</span></span>
  </nav>
</header>

<aside class="panel filters">
  <div class="f-title">Votre recherche:</div>
  <div class="field search-field">
    <svg width="10" height="10" viewBox="0 0 10 10" style="margin-right:6px"><circle cx="4" cy="4" r="3" fill="none" stroke="#aaa"/><line x1="6.3" y1="6.3" x2="9" y2="9" stroke="#aaa"/></svg>Ou cherchez-vous?
  </div>
  <div class="f-label" style="top:81px">Perimetre de recherche:</div>
  <div class="slider-track"><div class="slider-fill"></div><div class="slider-knob"></div></div>
  <div class="slider-value">20km</div>

  <div class="f-label" style="top:138px">Loyer par mois</div>
  <div class="field" style="left:11px;top:152px;width:98px">Min</div>
  <div class="field" style="left:113px;top:152px;width:51px">500</div>

  <div class="f-label" style="top:196px">Type de logement</div>
  <div class="field" style="left:11px;top:210px;width:68px">Maison</div>
  <div class="field" style="left:82px;top:210px;width:63px">Appartement</div>

  <div class="f-label" style="top:253px">Chambres Disponibles</div>
  <div class="field" style="left:11px;top:268px;width:28px">1</div>
  <div class="field" style="left:38px;top:268px;width:31px">2</div>
  <div class="field" style="left:68px;top:268px;width:35px">3</div>
  <div class="field" style="left:102px;top:268px;width:42px">4</div>

  <div class="option" style="top:306px"><span class="radio on"></span>Annonces avec photo</div>
  <div class="option" style="top:326px"><span class="radio"></span>Chambres Doubles</div>
  <div class="option" style="top:346px"><span class="radio on"></span>Meubles</div>
  <div class="option" style="top:366px"><span class="radio"></span>Courte Duree</div>

  <div class="f-label" style="top:395px">Age du Colocatire</div>
  <div class="field" style="left:11px;top:415px;width:78px">35 <span class="caret" style="margin-left:4px">▾</span></div>
  <div class="field" style="left:93px;top:415px;width:51px">40 <span class="caret" style="margin-left:4px">▾</span></div>

  <div class="f-label" style="top:459px">Sexe du Colocataire</div>
  <div class="field" style="left:11px;top:473px;width:68px">Homme</div>
  <div class="field" style="left:82px;top:473px;width:63px">Femme</div>

  <div class="f-label" style="top:516px">Situation du Colocataire</div>
  <div class="field" style="left:11px;top:531px;width:68px">Edudiant</div>
  <div class="field" style="left:82px;top:531px;width:63px">Salarie</div>

  <div class="divider"></div>
  <div class="member-title">
    <svg width="15" height="15" viewBox="0 0 15 15"><circle cx="7.5" cy="5" r="3.3" fill="none" stroke="#666"/><path d="M1.5 14c0-3.5 2.7-5.3 6-5.3s6 1.8 6 5.3z" fill="none" stroke="#666"/></svg>
    Membre basique
  </div>
  <p class="member-text" style="top:628px">Lorem ipsum dolor sit amet, consectetur adipisicing elit, sed do eiusmod tempor</p>
  <p class="member-text" style="top:682px">incididunt ut labore et dolore magna aliqua. Ut enim ad minim veniam, quis nostrud exercitation ullamco laboris nisi ut aliquip ex ea commodo</p>
  <div class="cta">Activer un pass</div>
</aside>

<main class="panel results">
  <div class="results-head">6 offres de colocation a paris-ile De France</div>
  <div class="sort-label">Trier par</div>
  <div class="sort-select">Plus recent <span class="caret">▾</span></div>

  <article class="listing" style="top:51px">
    <div class="listing-photo ph1" role="img" aria-label="Photo of a tall apartment tower under a blue sky"><span class="play"></span></div>
    <div class="price">€500<small>/Mois</small></div>
    <div class="listing-body">
      <div class="addr"><svg width="12" height="16" viewBox="0 0 12 16"><path d="M6 15S1 9 1 5.8a5 5 0 0 1 10 0C11 9 6 15 6 15z" fill="none" stroke="#888"/><circle cx="6" cy="6" r="1.8" fill="none" stroke="#888"/></svg>Allee Des Tilleuls, Vernay-s...</div>
      <div class="meta"><span class="badge">Membre Premium</span>Mis a jour il y a 1 jour</div>
      <div class="avail"><span>Disponible le 26 dec.</span><span>Non specifie</span></div>
      <div class="summary">Appartement loue meuble de 3ch, 100m2 a 5min a pie...</div>
      <p class="excerpt">Bonjiour, Je propose a partir du mois de decembre mon appartement libre pour en faire une colocation meublee.Il</p>
      <div class="tools"><svg width="12" height="10" viewBox="0 0 12 10"><rect x=".5" y=".5" width="11" height="9" fill="none" stroke="#777"/><path d="M1 9l3.5-4 2.5 3 2-2 2 3" fill="none" stroke="#777"/></svg><svg width="11" height="10" viewBox="0 0 11 10"><path d="M.5 4.5L10.5.5 7 9.5 5 5.5z" fill="none" stroke="#777"/></svg></div>
    </div>
  </article>

  <article class="listing" style="top:224px">
    <div class="listing-photo ph2" role="img" aria-label="Photo of a family house with a for-sale sign on the lawn"><span class="play"></span></div>
    <div class="price">€500<small>/Mois</small></div>
    <div class="listing-body">
      <div class="addr"><svg width="12" height="16" viewBox="0 0 12 16"><path d="M6 15S1 9 1 5.8a5 5 0 0 1 10 0C11 9 6 15 6 15z" fill="none" stroke="#888"/><circle cx="6" cy="6" r="1.8" fill="none" stroke="#888"/></svg>Allee Des Tilleuls, Vernay-s...</div>
      <div class="meta"><span class="badge">Membre Premium</span>Mis a jour il y a 1 jour</div>
      <div class="avail"><span>Disponible le 26 dec.</span><span>Non specifie</span></div>
      <div class="summary">Appartement loue meuble de 3ch, 100m2 a 5min a pie...</div>
      <p class="excerpt">Bonjiour, Je propose a partir du mois de decembre mon appartement libre pour en faire une colocation meublee.Il</p>
      <div class="tools"><svg width="12" height="10" viewBox="0 0 12 10"><rect x=".5" y=".5" width="11" height="9" fill="none" stroke="#777"/><path d="M1 9l3.5-4 2.5 3 2-2 2 3" fill="none" stroke="#777"/></svg><svg width="11" height="10" viewBox="0 0 11 10"><path d="M.5 4.5L10.5.5 7 9.5 5 5.5z" fill="none" stroke="#777"/></svg></div>
    </div>
  </article>

  <article class="listing" style="top:397px">
    <div class="listing-photo ph3" role="img" aria-label="Photo of a balcony with red flowers and a city skyline behind"><span class="play"></span></div>
    <div class="price">€500<small>/Mois</small></div>
    <div class="listing-body">
      <div class="addr"><svg width="12" height="16" viewBox="0 0 12 16"><path d="M6 15S1 9 1 5.8a5 5 0 0 1 10 0C11 9 6 15 6 15z" fill="none" stroke="#888"/><circle cx="6" cy="6" r="1.8" fill="none" stroke="#888"/></svg>Allee Des Tilleuls, Vernay-s...</div>
      <div class="meta"><span class="badge">Membre Premium</span>Mis a jour il y a 1 jour</div>
      <div class="avail"><span>Disponible le 26 dec.</span><span>Non specifie</span></div>
      <div class="summary">Appartement loue meuble de 3ch, 100m2 a 5min a pie...</div>
      <p class="excerpt">Bonjiour, Je propose a partir du mois de decembre mon appartement libre pour en faire une colocation meublee.Il</p>
      <div class="tools"><svg width="12" height="10" viewBox="0 0 12 10"><rect x=".5" y=".5" width="11" height="9" fill="none" stroke="#777"/><path d="M1 9l3.5-4 2.5 3 2-2 2 3" fill="none" stroke="#777"/></svg><svg width="11" height="10" viewBox="0 0 11 10"><path d="M.5 4.5L10.5.5 7 9.5 5 5.5z" fill="none" stroke="#777"/></svg></div>
    </div>
  </article>

  <article class="listing" style="top:570px">
    <div class="listing-photo ph4" role="img" aria-label="Photo of a suburban house with a large for-sale sign"><span class="play"></span></div>
    <div class="price">€500<small>/Mois</small></div>
    <div class="listing-body">
      <div class="addr"><svg width="12" height="16" viewBox="0 0 12 16"><path d="M6 15S1 9 1 5.8a5 5 0 0 1 10 0C11 9 6 15 6 15z" fill="none" stroke="#888"/><circle cx="6" cy="6" r="1.8" fill="none" stroke="#888"/></svg>Allee Des Tilleuls, Vernay-s...</div>
      <div class="meta"><span class="badge">Membre Premium</span>Mis a jour il y a 1 jour</div>
      <div class="avail"><span>Disponible le 26 dec.</span><span>Non specifie</span></div>
      <div class="summary">Appartement loue meuble de 3ch, 100m2 a 5min a pie...</div>
      <p class="excerpt">Bonjiour, Je propose a partir du mois de decembre mon appartement libre pour en faire une colocation meublee.Il</p>
      <div class="tools"><svg width="12" height="10" viewBox="0 0 12 10"><rect x=".5" y=".5" width="11" height="9" fill="none" stroke="#777"/><path d="M1 9l3.5-4 2.5 3 2-2 2 3" fill="none" stroke="#777"/></svg><svg width="11" height="10" viewBox="0 0 11 10"><path d="M.5 4.5L10.5.5 7 9.5 5 5.5z" fill="none" stroke="#777"/></svg></div>
    </div>
  </article>
</main>

<footer class="site-footer">
  <div class="f-head" style="left:235px">About real homes</div>
  <p class="f-text" style="left:238px;top:74px;width:195px">Lorem ipsum dolor sit amet, consectetur adipisicing elit, sed do eiusmod tempor incididunt ut labore et dolore magna aliqua. Ut enim ad minim veniam, quis nostrud exercitation ullamco laboris nisi ut aliquip ex ea commodo consequat.</p>

  <div class="f-head" style="left:466px">Quick links</div>
  <ul class="f-links" style="left:466px;top:72px"><li>Single Family</li><li>New construction</li><li>On rent</li><li>On sale</li></ul>
  <ul class="f-links" style="left:551px;top:72px"><li>Single Family</li><li>New construction</li><li>On rent</li><li>On sale</li></ul>

  <div class="f-head" style="left:645px">Latest info</div>
  <ul class="f-info"><li>Lorem ipsum dolor sit amet, consectetur adipisicing</li><li>Lorem ipsum dolor sit amet, consectetur</li><li>adipisicing elit, sed do eiusmod tempor incididunt</li></ul>

  <div class="f-head" style="left:798px">Address</div>
  <div class="contact-line" style="top:74px;width:125px"><svg width="10" height="13" viewBox="0 0 10 13"><path d="M5 12S1 7.5 1 4.8a4 4 0 0 1 8 0C9 7.5 5 12 5 12z" fill="none" stroke="#999"/><circle cx="5" cy="5" r="1.4" fill="none" stroke="#999"/></svg><span>niam, quis nostrud exercitn lamco laboris nisi ut aliquip ex ea, London</span></div>
  <div class="contact-line" style="top:124px"><svg width="14" height="10" viewBox="0 0 14 10"><rect x=".5" y=".5" width="13" height="9" fill="none" stroke="#999"/><path d="M.5.5l6.5 5 6.5-5" fill="none" stroke="#999"/></svg><span>hello@harbornestmail.com</span></div>
  <div class="contact-line" style="top:143px"><svg width="13" height="13" viewBox="0 0 13 13"><path d="M3 1l2 3-1.3 1.3a7 7 0 0 0 4 4L9 8l3 2-1.5 2C5.5 12 1 7.5 1 2.5z" fill="none" stroke="#999"/></svg><span>+16540 2233 7781</span></div>

  <div class="footer-rule"></div>
  <div class="copy" style="left:235px">@All right reserved by the company 2015.</div>
  <div class="copy" style="left:808px">Designed by OwnerName</div>
</footer>

</body>
</html>
```